Modern Business Card for Larkwell 2018

Our company assumes the best about people. We are creating an online community of entrepreneurs and business leaders who struggle with marketing their business online.

This business card should POP! We recently got a new logo and are launching a new website next month, so our business cards should make a statement that feels:
-Fresh
-Smart
-Trustworthy
-Fun

Target Market(s)

small business owners, entrepreneurs

Industry/Entity Type

Digital Marketing

Contact Information for Business Card

Dimensions: 3.5" x 2"

Font styles to use
Sans Serif

Colors
f37122
ffffff

Requirements
Must have
• We need a business card with a modern, bold design. We will use one side of the card as a lead-generation offer, so text on one side will need to fit up to 140 characters. The business card should stick to our core colors (orange, black, and white).
Nice to have
• We think a vertical "portrait" design could be interesting.
Should not have
• Should not look like a traditional business card. The round icon should stand out from a distance.

```html
<!DOCTYPE html>
<html lang="en">
<head>
<meta charset="utf-8">
<title>Larkwell Business Card</title>
<link rel="stylesheet" href="https://fonts.googleapis.com/css2?family=Work+Sans:wght@400;500;600;800&display=swap">
<style>
  :root {
    --orange: #f37122;
    --orange-deep: #ef5a20;
    --ink: #2b2b2b;
    --white: #ffffff;
    --backdrop: #cde9e0;
  }
  * { box-sizing: border-box; margin: 0; padding: 0; }
  html, body { width: 1200px; height: 856px; overflow: hidden; }
  body {
    background: var(--backdrop);
    font-family: "Work Sans", Arial, sans-serif;
    display: flex;
    align-items: center;
    justify-content: center;
    gap: 40px;
  }
  .card {
    width: 560px;
    height: 320px;
    border-radius: 26px;
    position: relative;
    overflow: hidden;
    box-shadow: 0 10px 30px rgba(40, 90, 80, 0.18);
  }

  /* Front */
  .card-front {
    background: var(--white);
    display: flex;
    align-items: center;
    padding: 0 36px 0 40px;
  }
  .front-brand {
    width: 240px;
    display: flex;
    flex-direction: column;
    align-items: center;
    gap: 14px;
  }
  .brand-dot {
    width: 40px; height: 40px;
    border-radius: 50%;
    background: var(--orange);
  }
  .brand-name {
    font-weight: 800;
    font-size: 44px;
    letter-spacing: 1px;
    color: var(--ink);
    line-height: 1;
  }
  .divider {
    width: 2px;
    height: 150px;
    background: var(--ink);
    margin: 0 22px 0 10px;
  }
  .contact { color: var(--ink); font-size: 13.5px; line-height: 1.35; }
  .contact-name {
    color: var(--orange);
    font-weight: 600;
    font-size: 21px;
    letter-spacing: 1px;
    line-height: 1.1;
  }
  .contact-title { font-size: 14px; margin-bottom: 12px; }
  .contact-address { margin-bottom: 10px; }
  .contact-list { list-style: none; }
  .contact-list li { display: flex; align-items: center; gap: 8px; }
  .contact-list svg { width: 11px; height: 11px; flex: none; }
  .web-accent { color: var(--orange); }

  /* Back */
  .card-back {
    background: linear-gradient(160deg, var(--orange) 0%, var(--orange-deep) 100%);
    color: var(--white);
    display: flex;
    flex-direction: column;
    align-items: center;
    padding-top: 56px;
  }
  .world-map {
    position: absolute;
    left: 70px; top: 30px;
    width: 420px; height: 200px;
    border-radius: 40px;
    background: radial-gradient(ellipse at center, rgba(255,255,255,0.12) 0%, rgba(255,255,255,0) 70%);
  }
  .back-brand {
    position: relative;
    display: flex;
    flex-direction: column;
    align-items: center;
    gap: 12px;
  }
  .card-back .brand-dot { background: var(--white); width: 38px; height: 38px; }
  .card-back .brand-name { color: var(--white); font-size: 46px; }
  .offer {
    position: relative;
    margin-top: 22px;
    font-size: 11px;
    text-align: center;
    line-height: 1.35;
  }
  .back-rule {
    position: relative;
    width: 440px;
    height: 1px;
    background: rgba(255,255,255,0.85);
    margin-top: 10px;
  }
  .tagline {
    position: relative;
    margin-top: 8px;
    font-size: 13px;
    font-weight: 500;
    letter-spacing: 0.3px;
  }
</style>
</head>
<body>
  <section class="card card-front" aria-label="Business card front">
    <div class="front-brand">
      <span class="brand-dot"></span>
      <span class="brand-name">LARKWELL</span>
    </div>
    <div class="divider"></div>
    <div class="contact">
      <p class="contact-name">DANA WHITLOW</p>
      <p class="contact-title">Story Marketing Coach</p>
      <p class="contact-address">NR2040, 18/3 Linden Row<br>Harbor city, Norland</p>
      <ul class="contact-list">
        <li>
          <svg viewBox="0 0 12 12"><path d="M2.5 1 L4.5 1 L5.2 3.6 L3.9 4.6 Q5 7 7.4 8.1 L8.4 6.8 L11 7.5 L11 9.5 Q10.5 11 9 11 Q1 10 1 3 Q1 1.5 2.5 1 Z" fill="var(--orange)"/></svg>
          (555) 014-2290
        </li>
        <li>
          <svg viewBox="0 0 12 12"><rect x="1" y="2.5" width="10" height="7" fill="none" stroke="var(--orange)" stroke-width="1.2"/><path d="M1 2.5 L6 6.5 L11 2.5" fill="none" stroke="var(--orange)" stroke-width="1.2"/></svg>
          Dana@larkwellnow.com
        </li>
        <li>
          <svg viewBox="0 0 12 12"><circle cx="6" cy="6" r="5" fill="none" stroke="var(--orange)" stroke-width="1.1"/><ellipse cx="6" cy="6" rx="2.2" ry="5" fill="none" stroke="var(--orange)" stroke-width="1"/><path d="M1 6 H11" stroke="var(--orange)" stroke-width="1"/></svg>
          <span>www.<span class="web-accent">larkwellnow</span>.com</span>
        </li>
      </ul>
    </div>
  </section>

  <section class="card card-back" aria-label="Business card back">
    <div class="world-map" role="img" aria-label="Faint dotted world map behind the logo"></div>
    <div class="back-brand">
      <span class="brand-dot"></span>
      <span class="brand-name">LARKWELL</span>
    </div>
    <p class="offer">Get your free Larkwell<br>Starter Package and our marketing guide today at</p>
    <div class="back-rule"></div>
    <p class="tagline">REACH MORE PEOPLE. MAKE MORE MONEY. CREATE MORE IMPACT.</p>
  </section>
</body>
</html>
```